Vantro cards

I am in the auto motive, transportation business I would like a business card that is Something cool, modern edgy, having to do with car culture. I offer towing service for high and exotic cars. I also provide towing for collisions and car accidents. I offer open and enclosed transport nationwide.

Target Market(s)

Car culture people high end auto collectors

Industry/Entity Type

Towing car carrier

Contact Information for Business Card

My company colors black yellow and silver

Font styles to use
Serif

```html
<!DOCTYPE html>
<html lang="en">
<head>
<meta charset="utf-8">
<title>Vantro Business Card</title>
<link href="https://fonts.googleapis.com/css2?family=Arimo:wght@400;700&display=swap" rel="stylesheet">
<style>
  :root {
    --backdrop: #2b2b2b;
    --card: #1e1e1e;
    --card-back: #171717;
    --yellow: #f9e05a;
    --silver: #b9b9bb;
    --white: #ffffff;
    --ink: #161616;
    --rule: #8a8a8a;
  }
  * { margin: 0; padding: 0; box-sizing: border-box; }
  html, body { width: 1200px; height: 1200px; overflow: hidden; }
  body {
    background: var(--backdrop);
    font-family: "Arimo", Arial, sans-serif;
    position: relative;
  }
  .card {
    position: absolute;
    top: 240px;
    width: 420px;
    height: 720px;
    border-radius: 28px;
    overflow: hidden;
  }
  .card-front { left: 150px; background: var(--card); }
  .card-back { left: 630px; background: var(--card-back); }

  .brand-mark {
    position: absolute;
    left: 0; right: 0;
    display: flex;
    align-items: center;
    justify-content: center;
    gap: 14px;
  }
  .brand-mark .brand-square {
    width: 22px; height: 22px;
    background: var(--yellow);
  }
  .brand-mark .brand-name {
    color: var(--silver);
    font-weight: 700;
    letter-spacing: 3px;
  }
  .card-front .brand-mark { top: 150px; }
  .card-front .brand-name { font-size: 58px; }
  .card-back .brand-mark { top: 560px; }
  .card-back .brand-name { font-size: 44px; }

  .name-band {
    position: absolute;
    top: 326px; left: 0; right: 0;
    height: 104px;
    background: var(--yellow);
    color: var(--ink);
    text-align: center;
    padding-top: 24px;
  }
  .name-band .person-name {
    font-size: 29px; font-weight: 700; letter-spacing: 1px;
  }
  .name-band .person-title {
    font-size: 20px; margin-top: 4px;
  }

  .contact-divider {
    position: absolute;
    top: 470px; left: 40px; right: 40px;
    display: flex; align-items: center; gap: 12px;
  }
  .contact-divider .rule { flex: 1; height: 1px; background: var(--rule); }
  .contact-icons { display: flex; gap: 8px; }
  .contact-icons .icon {
    width: 26px; height: 26px;
    background: var(--yellow);
    border-radius: 5px;
    display: flex; align-items: center; justify-content: center;
  }
  .contact-list {
    position: absolute;
    top: 502px; left: 0; right: 0;
    text-align: center;
    color: var(--white);
    font-size: 19px;
    line-height: 30px;
  }
  .address-rule {
    position: absolute;
    top: 636px; left: 40px; right: 40px;
    height: 1px; background: var(--rule);
  }
  .address {
    position: absolute;
    top: 652px; left: 0; right: 0;
    text-align: center;
    color: var(--white);
    font-size: 19px;
    line-height: 27px;
  }
</style>
</head>
<body>
  <section class="card card-front">
    <div class="brand-mark">
      <span class="brand-square"></span>
      <span class="brand-name">VANTRO</span>
    </div>

    <div class="name-band">
      <div class="person-name">DORIAN KESSLER</div>
      <div class="person-title">CEO/Founder</div>
    </div>

    <div class="contact-divider">
      <span class="rule"></span>
      <div class="contact-icons">
        <span class="icon" aria-label="Phone">
          <svg width="14" height="14" viewBox="0 0 24 24"><path d="M6 2l4 4-2 3c1 3 4 6 7 7l3-2 4 4-3 4C10 22 2 14 2 5z" fill="#161616"/></svg>
        </span>
        <span class="icon" aria-label="Mobile">
          <svg width="14" height="14" viewBox="0 0 24 24"><rect x="6" y="2" width="12" height="20" rx="2" fill="none" stroke="#161616" stroke-width="2.4"/><circle cx="12" cy="18" r="1.3" fill="#161616"/></svg>
        </span>
        <span class="icon" aria-label="Email">
          <svg width="14" height="14" viewBox="0 0 24 24"><rect x="2" y="5" width="20" height="14" fill="#161616"/><path d="M2 5l10 8 10-8" fill="none" stroke="#f9e05a" stroke-width="2"/></svg>
        </span>
        <span class="icon" aria-label="Website">
          <svg width="14" height="14" viewBox="0 0 24 24" fill="none" stroke="#161616" stroke-width="2"><circle cx="12" cy="12" r="9.5"/><ellipse cx="12" cy="12" rx="4" ry="9.5"/><path d="M2.5 12h19M4 7h16M4 17h16"/></svg>
        </span>
      </div>
      <span class="rule"></span>
    </div>

    <div class="contact-list">
      <div>(555) 201 4478</div>
      <div>(555) 309 6612</div>
      <div>info@vantrotransport.com</div>
      <div>www.vantrotransport.com</div>
    </div>

    <div class="address-rule"></div>
    <div class="address">
      <div>P.O. Box 7310 Street</div>
      <div>Country Name AB 4196</div>
    </div>
  </section>

  <section class="card card-back">
    <div class="brand-mark">
      <span class="brand-square"></span>
      <span class="brand-name">VANTRO</span>
    </div>
  </section>
</body>
</html>
```